School Poster

Design so that these can be placed in classrooms across the school.

Attached is another design we have had done. Use a similar theme.

Consider using themes from https://corvalhs.edq.example.au/

please edit Binder1 doc.

Students and teachers

```html
<!DOCTYPE html>
<html lang="en">
<head>
<meta charset="utf-8">
<title>Before You Ask the Teacher – Corval State High School</title>
<link rel="stylesheet" href="https://fonts.googleapis.com/css2?family=Roboto:wght@400;500;700;900&display=swap">
<style>
  :root {
    --navy: #263a7c;
    --navy-line: #3b4ea0;
    --yellow: #f2e34c;
    --card: #d8d9ec;
    --card-stripe: #bdbfdd;
    --pale: #faf7dc;
    --pale-mid: #f4ec98;
    --divider: #efe27a;
    --ink: #1b1b1b;
    --stage: #d4d4d4;
  }
  * { box-sizing: border-box; margin: 0; padding: 0; }
  html, body { width: 1200px; height: 1200px; overflow: hidden; background: var(--stage); }
  body { font-family: "Roboto", Arial, sans-serif; color: var(--ink); position: relative; }

  .poster {
    position: absolute; left: 191px; top: 23px;
    width: 1168px; height: 1649px;
    background: #fff;
    transform: scale(0.7); transform-origin: 0 0;
    overflow: hidden;
  }
  .header-shapes { position: absolute; left: 0; top: 0; }

  .school-name {
    position: absolute; left: 70px; top: 120px; width: 200px;
    display: flex; flex-direction: column; align-items: center; gap: 10px;
    font-weight: 700; font-size: 28px; color: var(--navy); text-align: center; line-height: 1.1;
  }
  .school-name .mark { width: 56px; height: 56px; border-radius: 50%; background: var(--navy); }

  .title-top {
    position: absolute; left: 310px; top: 44px;
    font-weight: 900; font-size: 45px; color: var(--yellow); letter-spacing: 0.5px;
  }
  .title-main {
    position: absolute; left: 310px; top: 126px;
    font-weight: 900; font-size: 65px; color: var(--navy); letter-spacing: 0.5px;
  }

  .card {
    position: absolute; top: 292px; height: 518px;
    background: var(--card); border: 2px solid var(--navy-line);
  }
  .card--think { left: 18px; width: 314px; }
  .card--check { left: 345px; width: 433px; }
  .card--ask   { left: 792px; width: 358px; }

  .card-pill {
    position: absolute; top: -24px; left: 10px; right: -10px; height: 46px;
    background: var(--yellow); border-radius: 23px;
    display: flex; align-items: center;
    font-weight: 700; font-size: 27px; color: var(--navy);
  }
  .card--check .card-pill { right: 10px; }
  .card--ask .card-pill { right: -10px; }
  .card-pill .num {
    width: 48px; height: 46px; border-radius: 23px 0 0 23px; background: var(--navy);
    color: #fff; display: flex; align-items: center; justify-content: center;
    font-size: 25px; margin-right: 24px;
  }
  .card-icon {
    position: absolute; top: 35px; left: 50%; margin-left: -44px;
    width: 88px; height: 88px;
  }
  .card-head {
    position: absolute; left: 18px; right: 10px; top: 124px;
    font-weight: 700; font-size: 26px; line-height: 31px; color: var(--navy);
  }
  .card--check .card-head { left: 28px; }

  .card-list { position: absolute; left: 0; right: 0; list-style: none; }
  .card--think .card-list { top: 211px; }
  .card--check .card-list { top: 178px; }
  .card--ask .card-list { top: 210px; }
  .card-list li {
    display: flex; align-items: center; position: relative;
    padding-left: 46px; padding-right: 8px;
    font-size: 25px; line-height: 31px;
  }
  .card-list li:nth-child(odd) { background: var(--card-stripe); }
  .card--check .card-list li { padding-left: 54px; }
  .card-list li::before {
    content: ""; position: absolute; left: 18px; top: 50%; margin-top: -4px;
    width: 9px; height: 9px; border-radius: 50%; background: var(--navy-line);
  }
  .card--check .card-list li::before { left: 26px; }
  .row-2 { height: 76px; }
  .row-1 { height: 47px; }
  .row-lead { height: 70px; }
  .card-note {
    position: absolute; left: 16px; right: 10px; top: 440px;
    font-size: 25px; line-height: 31px;
  }

  .motto {
    position: absolute; left: 195px; top: 834px; width: 773px; height: 47px;
    background: var(--navy); border-radius: 24px;
    display: flex; align-items: center; justify-content: center;
    font-weight: 700; font-size: 30px; letter-spacing: 3.5px; color: #fff;
  }
  .motto .accent { color: var(--yellow); margin: 0 14px; }

  .ai-banner {
    position: absolute; left: 0; top: 910px; width: 100%; height: 70px;
    background: var(--yellow);
    display: flex; align-items: center; justify-content: center;
    font-weight: 900; font-size: 51px; color: var(--navy); letter-spacing: 1px;
  }

  .rules-bg { position: absolute; left: 0; top: 1017px; width: 100%; height: 550px; background: var(--pale); }
  .rules-bg .mid { position: absolute; left: 368px; top: 0; width: 377px; height: 100%; background: var(--pale-mid); }

  .rule-head {
    position: absolute; top: 1033px; height: 128px;
    background: var(--navy); border-radius: 10px;
    display: flex; align-items: center; justify-content: center; text-align: center;
    color: #fff; font-weight: 700; font-size: 27px; line-height: 32px;
    padding-top: 8px;
  }
  .rule-head--must { left: 18px; width: 342px; }
  .rule-head--help { left: 376px; width: 361px; }
  .rule-head--cannot { left: 752px; width: 396px; }
  .rule-mark { position: absolute; top: 1005px; width: 48px; height: 48px; }

  .rule-list { position: absolute; top: 1172px; list-style: none; }
  .rule-list--must { left: 23px; width: 332px; }
  .rule-list--help { left: 383px; width: 346px; }
  .rule-list--cannot { left: 760px; width: 388px; }
  .rule-list li {
    position: relative; padding: 7px 6px 14px 32px;
    font-size: 25px; line-height: 31px;
    border-bottom: 2px solid var(--divider);
  }
  .rule-list li:last-child { border-bottom: none; }
  .rule-list li::before {
    content: ""; position: absolute; left: 12px; top: 19px;
    width: 8px; height: 8px; border-radius: 50%; background: var(--navy-line);
  }

  .footer-bar {
    position: absolute; left: 0; top: 1591px; width: 100%; height: 38px;
    background: var(--navy);
    display: flex; align-items: center; justify-content: center;
    color: var(--yellow); font-weight: 700; font-size: 21px; letter-spacing: 2.2px;
  }
</style>
</head>
<body>
<main class="poster">
  <svg class="header-shapes" width="1168" height="160" viewBox="0 0 1168 160" aria-hidden="true">
    <path d="M0 0 H65 V115 L0 119 Z" fill="#263a7c"/>
    <path d="M0 119 L65 115 V138 L0 142 Z" fill="#f2e34c"/>
    <path d="M275 0 H1168 V135 Q720 88 275 108 Z" fill="#263a7c"/>
  </svg>

  <div class="school-name"><span class="mark"></span>Corval SHS</div>

  <h1 class="title-top">BEFORE YOU ASK THE TEACHER.....</h1>
  <h2 class="title-main">TRY THESE STEPS FIRST!</h2>

  <section class="card card--think">
    <div class="card-pill"><span class="num">1</span>THINK FIRST</div>
    <svg class="card-icon" viewBox="0 0 88 88" aria-hidden="true">
      <circle cx="44" cy="44" r="42" fill="#263a7c" stroke="#f2e34c" stroke-width="3"/>
      <g fill="none" stroke="#f2e34c" stroke-width="3">
        <circle cx="44" cy="44" r="9"/>
        <path d="M44 24v8M44 56v8M24 44h8M56 44h8M30 30l6 6M52 52l6 6M58 30l-6 6M36 52l-6 6"/>
      </g>
    </svg>
    <p class="card-head">Don’t give up straight away</p>
    <ul class="card-list">
      <li class="row-2">Read the question carefully</li>
      <li class="row-2">Identify what you already know</li>
      <li class="row-2">Try a strategy you’ve used before</li>
      <li class="row-2">Give yourself thinking time</li>
    </ul>
  </section>

  <section class="card card--check">
    <div class="card-pill"><span class="num">2</span>CHECK YOUR SUPPORTS</div>
    <svg class="card-icon" viewBox="0 0 88 88" aria-hidden="true">
      <circle cx="44" cy="44" r="42" fill="#263a7c" stroke="#f2e34c" stroke-width="3"/>
      <g fill="none" stroke="#fff" stroke-width="2.5">
        <path d="M30 22h22l10 10v34H30z"/>
        <path d="M52 22v10h10M38 40h18M38 48h18M42 56h14"/>
        <circle cx="32" cy="58" r="8" fill="#263a7c"/>
        <path d="M28 58l3 3 5-6"/>
      </g>
    </svg>
    <p class="card-head">Before asking for help, check:</p>
    <ul class="card-list">
      <li class="row-lead">Learning goal and success criteria</li>
      <li class="row-1">Worked examples</li>
      <li class="row-1">Class notes</li>
      <li class="row-1">Classroom displays</li>
      <li class="row-1">LearnHub resources</li>
      <li class="row-1">Task sheet and instructions</li>
    </ul>
  </section>

  <section class="card card--ask">
    <div class="card-pill"><span class="num">3</span>ASK 3 BEFORE ME</div>
    <svg class="card-icon" viewBox="0 0 88 88" aria-hidden="true">
      <circle cx="44" cy="44" r="42" fill="#263a7c" stroke="#f2e34c" stroke-width="3"/>
      <g fill="none" stroke="#fff" stroke-width="2.5">
        <path d="M20 24h30v20H30l-6 6v-6h-4z"/>
        <path d="M40 38h28v22h-4v6l-6-6H40z" fill="#263a7c"/>
        <path d="M46 46h16M46 52h16"/>
      </g>
      <text x="35" y="39" font-family="Roboto, sans-serif" font-size="14" font-weight="700" fill="#fff">?</text>
    </svg>
    <p class="card-head">Ask three sources before asking the teacher:</p>
    <ul class="card-list">
      <li class="row-2">A person (partner or neighbour)</li>
      <li class="row-2">A place (notes, display, LearnHub)</li>
      <li class="row-2">A resource (worked example, task sheet)</li>
    </ul>
    <p class="card-note">Then ask the teacher if you still need help</p>
  </section>

  <p class="motto">WE BELIEVE.<span class="accent">WE STRIVE.</span>WE ACHIEVE</p>

  <h2 class="ai-banner">USING AI AND OTHER TOOLS RESPONSIBLY</h2>

  <div class="rules-bg"><div class="mid"></div></div>

  <h3 class="rule-head rule-head--must">WHAT YOU MUST DO</h3>
  <h3 class="rule-head rule-head--help">WHAT AI CAN HELP YOU DO (WHEN APPROVED BY YOUR TEACHER)</h3>
  <h3 class="rule-head rule-head--cannot">WHAT YOU CANNOT DO</h3>

  <svg class="rule-mark" style="left:165px" viewBox="0 0 48 48" aria-hidden="true">
    <circle cx="24" cy="24" r="22" fill="#263a7c" stroke="#f2e34c" stroke-width="3"/>
    <path d="M13 24l8 8 14-15" fill="none" stroke="#f2e34c" stroke-width="5" stroke-linecap="round" stroke-linejoin="round"/>
  </svg>
  <svg class="rule-mark" style="left:533px" viewBox="0 0 48 48" aria-hidden="true">
    <circle cx="24" cy="24" r="22" fill="#263a7c" stroke="#f2e34c" stroke-width="3"/>
    <path d="M13 24l8 8 14-15" fill="none" stroke="#f2e34c" stroke-width="5" stroke-linecap="round" stroke-linejoin="round"/>
  </svg>
  <svg class="rule-mark" style="left:928px" viewBox="0 0 48 48" aria-hidden="true">
    <circle cx="24" cy="24" r="22" fill="#263a7c" stroke="#f2e34c" stroke-width="3"/>
    <path d="M15 15l18 18M33 15L15 33" fill="none" stroke="#f2e34c" stroke-width="5" stroke-linecap="round"/>
  </svg>

  <ul class="rule-list rule-list--must">
    <li>Complete your own work</li>
    <li>Demonstrate your progress (drafts, notes, planning, revisions)</li>
    <li>Use feedback to improve your work</li>
    <li>Demonstrate your understanding of the ideas in your submission</li>
  </ul>
  <ul class="rule-list rule-list--help">
    <li>Complete your own work</li>
    <li>Demonstrate your progress (drafts, notes, planning, revisions)</li>
    <li>Use feedback to improve your work</li>
    <li>Demonstrate your understanding of the ideas in your submission</li>
  </ul>
  <ul class="rule-list rule-list--cannot">
    <li>Submit AI generated work as your own</li>
    <li>Copy and paste AI responses without acknowledging or adapting them</li>
    <li>Use AI tools to complete the whole task for you</li>
    <li>Submit work that does not demonstrate your understanding</li>
  </ul>

  <p class="footer-bar">IF YOU DIDN’T CREATE, DEVELOP AND UNDERSTAND IT, IT ISN’T YOUR WORK.</p>
</main>
</body>
</html>
```